Website Comps for Famous Southern BBQ Restaurant in Alabama

We need an authentic, brand-focused redesign for a restaurant.

We need an authentic look.
The client really likes this website.
https://pelmarsmokehouse.example/

I don't want to see a bunch of crazy colors.
Avoid image sliders on the homepage. I hate those.

Please mockup the following three pages:
Homepage
Interior page (for mockup purposes, you can do an About page)
Menu page

I only need the PSD's; not the website coded.

Here is the current website: www.kortiespit.example

https://pelmarsmokehouse.example/

Here are some additional stock photos. New photos will be shot, but these may help for your mock-up designs.
https://files.quillbox.example/sh/83kkqvtrd41zpa7/XQM20PbT9LyRk-wnEuvJ3tpd?dl=0
Updates

I realize we don't have a lot of high-quality photos to work with.Those will be shot.Here are some additional stock photos that may help.https://files.quillbox.example/sh/83kkqvtrd41zpa7/XQM20PbT9LyRk-wnEuvJ3tpd?dl=0 Added Saturday, June 10, 2017

Target Market(s)

United states

Industry/Entity Type

Restaurant

Number of Pages Required

3 page

Font styles to use
Sans Serif

Colors

Designer to choose colors to be used in the design.

Requirements
Must have
• An authentic look.
• The client really likes this website.
• https://pelmarsmokehouse.example/
• It's simple, bold, and vintage at the same time.
• That is what we want.
• Our existing website is
• kortiespit.example
Nice to have
• Simplicity. Something that makes the food look good.
• Possibly a background.
• Logo:
• https://files.quillbox.example/s/t62bnezwhk0qpl3/kories-pit-lakeview.png?dl=0
• Here is a sampling of photos for your comps:
• https://files.quillbox.example/sh/59ryhdupqv2ncmx/MPT4c1ZLvWeQjHoNUyrA8BfxKs?dl=0
Should not have
• Nothing too busy.
• Not too many colors.
• Keep it simple, authentic, "down home."
• No homepage image sliders.

```html
<!DOCTYPE html>
<html lang="en">
<head>
<meta charset="utf-8">
<title>Special Offer and Food Gallery</title>
<link rel="stylesheet" href="https://fonts.googleapis.com/css2?family=Oswald:wght@700&family=Lato:wght@400&family=Roboto+Condensed:wght@400&display=swap">
<style>
  :root {
    --accent: #f5921e;
    --ink-dark: #3b170b;
    --ink-muted: #555555;
    --ink-filter: #7a7a7a;
    --star: #f4c20d;
    --paper: #ffffff;
    --night: #141414;
  }
  * { margin: 0; padding: 0; box-sizing: border-box; }
  html, body { width: 1200px; height: 1200px; overflow: hidden; background: var(--paper); }
  body { position: relative; font-family: 'Lato', sans-serif; }

  .section-title {
    font-family: 'Oswald', sans-serif;
    font-weight: 700;
    color: var(--accent);
    text-align: center;
    letter-spacing: 0.5px;
    line-height: 1;
  }
  .section-subtitle { text-align: center; font-size: 14px; line-height: 1; }
  .divider-flourish {
    position: absolute; left: 527px; width: 146px; height: 18px; border-radius: 9px;
  }

  /* Special offer */
  .offer {
    position: absolute; left: 0; top: 0; width: 1200px; height: 542px;
    background: radial-gradient(ellipse at 40% 30%, #3a3633 0%, #242120 45%, var(--night) 100%);
  }
  .offer .section-title { position: absolute; top: 62px; width: 100%; font-size: 38px; }
  .offer .section-subtitle { position: absolute; top: 108px; width: 100%; color: #f2f2f2; }
  .offer .divider-flourish { top: 135px; background: linear-gradient(90deg, transparent, rgba(255,255,255,0.35), transparent); }

  .offer-card {
    position: absolute; top: 202px; width: 216px; height: 225px;
    background: var(--paper); padding: 7px;
  }
  .offer-card__photo { width: 100%; height: 211px; }
  .offer-card__label {
    position: absolute; left: 26px; top: 170px; width: 164px; height: 93px;
    background: var(--paper); text-align: center;
  }
  .offer-card__name { margin-top: 20px; font-size: 16px; color: var(--ink-muted); line-height: 1; }
  .offer-card__meta { display: flex; align-items: center; justify-content: space-between; padding: 0 16px 0 15px; margin-top: 13px; }
  .offer-card__price { font-family: 'Oswald', sans-serif; font-weight: 700; font-size: 26px; color: var(--ink-dark); line-height: 1; }
  .offer-card__stars { color: var(--star); font-size: 13px; letter-spacing: 1px; }

  /* Gallery */
  .gallery .section-title { position: absolute; top: 624px; width: 100%; font-size: 42px; }
  .gallery .section-subtitle { position: absolute; top: 679px; width: 100%; color: var(--ink-muted); }
  .gallery .divider-flourish { top: 706px; background: linear-gradient(90deg, transparent, rgba(60,60,60,0.3), transparent); }

  .gallery-filters {
    position: absolute; top: 768px; width: 100%;
    display: flex; justify-content: center; gap: 23px;
    list-style: none; font-family: 'Roboto Condensed', sans-serif; font-size: 15px; color: var(--ink-filter);
  }
  .gallery-filters .is-active { color: var(--accent); }

  .gallery-tile { position: absolute; }
</style>
</head>
<body>

<section class="offer">
  <h2 class="section-title">OUR SPECIAL OFFER</h2>
  <p class="section-subtitle">Praesent Rutrum Pretium Urna</p>
  <div class="divider-flourish" role="img" aria-label="Decorative scroll flourish divider"></div>

  <article class="offer-card" style="left:147px">
    <div class="offer-card__photo" role="img" aria-label="Cheeseburger with lettuce and tomato" style="background:linear-gradient(160deg,#5a2e1a,#9a5a2c 50%,#d8c6b0)"></div>
    <div class="offer-card__label">
      <h3 class="offer-card__name">QUIS ANTE</h3>
      <div class="offer-card__meta"><span class="offer-card__price">20$</span><span class="offer-card__stars">★★★★☆</span></div>
    </div>
  </article>

  <article class="offer-card" style="left:378px">
    <div class="offer-card__photo" role="img" aria-label="Smoked chicken with white sauce and sides" style="background:linear-gradient(160deg,#e4dcd2,#8a4a26 55%,#3a2518)"></div>
    <div class="offer-card__label">
      <h3 class="offer-card__name">QUIS ANTE</h3>
      <div class="offer-card__meta"><span class="offer-card__price">20$</span><span class="offer-card__stars">★★★★☆</span></div>
    </div>
  </article>

  <article class="offer-card" style="left:608px">
    <div class="offer-card__photo" role="img" aria-label="Iced fruit drink with sauce bottles" style="background:linear-gradient(160deg,#d08a1c,#c9502a 50%,#3a1a14)"></div>
    <div class="offer-card__label">
      <h3 class="offer-card__name">QUIS ANTE</h3>
      <div class="offer-card__meta"><span class="offer-card__price">20$</span><span class="offer-card__stars">★★★★☆</span></div>
    </div>
  </article>

  <article class="offer-card" style="left:838px">
    <div class="offer-card__photo" role="img" aria-label="Shrimp and grits in a white bowl" style="background:linear-gradient(170deg,#e9e6e2,#f3efe8 45%,#d49a3e 75%,#c8c3bd)"></div>
    <div class="offer-card__label">
      <h3 class="offer-card__name">QUIS ANTE</h3>
      <div class="offer-card__meta"><span class="offer-card__price">20$</span><span class="offer-card__stars">★★★★☆</span></div>
    </div>
  </article>
</section>

<section class="gallery">
  <h2 class="section-title">FOOD GALLERY</h2>
  <p class="section-subtitle">Lisis Pretium Nunc</p>
  <div class="divider-flourish" role="img" aria-label="Decorative scroll flourish divider"></div>

  <ul class="gallery-filters">
    <li class="is-active">All Items</li>
    <li>Bevrages</li>
    <li>Starter</li>
    <li>Meat</li>
    <li>Vegeterian</li>
    <li>Desserts</li>
  </ul>

  <div class="gallery-tile" style="left:147px;top:815px;width:447px;height:207px;background:linear-gradient(120deg,#b06a24,#e0a95a 45%,#d8c9a8 75%,#2a1a12)" role="img" aria-label="Fried fritters with dipping sauce"></div>
  <div class="gallery-tile" style="left:599px;top:815px;width:224px;height:207px;background:linear-gradient(160deg,#6a5a3a,#c9c2b6 50%,#5a3a22)" role="img" aria-label="Plated barbecue with greens and bread on a serving line"></div>
  <div class="gallery-tile" style="left:829px;top:815px;width:224px;height:207px;background:linear-gradient(160deg,#8a7a6a,#7a3a1c 50%,#2a1a14)" role="img" aria-label="Barbecued chicken quarter with sides"></div>
  <div class="gallery-tile" style="left:147px;top:1027px;width:224px;height:101px;background:linear-gradient(180deg,#c9a47a,#4a3424 60%,#b03a1a)" role="img" aria-label="Restaurant counter with sauce bottles"></div>
  <div class="gallery-tile" style="left:377px;top:1027px;width:224px;height:101px;background:linear-gradient(180deg,#3a3a3a,#8a7a6c 55%,#c9c4c0)" role="img" aria-label="Restaurant staff member at the counter"></div>
  <div class="gallery-tile" style="left:606px;top:1027px;width:447px;height:101px;background:linear-gradient(100deg,#d9cfc4,#c23a24 40%,#8a3a1c 60%,#c25a2a)" role="img" aria-label="Burger with sweet potato fries"></div>
</section>

</body>
</html>
```